birchwell hollow cattle company website

we would like a home page, an about us page, a page for sires, a page for dams, A sale page where we can list progreny for sale and a contact us. on the about us page we would like there to be a family picture. on the sires page we would like to have a picture of each sire, a description beside them and a link to their online profile at northern hereford registry. on the dam page we would like to have a picture of each dam, aswell as a description beside them aswell as a link to the northern hereford registry site. would like the website to very mobile phone friendly as expecting most traffic to be on phone. we would like the website to look and feel very mich like a farm, rustic, barbed wire and other farm feels. we would also like a frozen genetics pages where we can include pictures and descriptions of the sires and dams aswell as a price for embryos and semen. we need to website to be easy to maintain so we can update pictures and information as it changes, we would like there to be a feature so that people can sign up to be on our mailing list by giving us their mailing addess and email and full name
aswell as an area where they can send us a message to contact us.

leaving for work for 3 weeks in the canadian arctic will have limited ability to use the internet

Target Market(s)

other ranchers, farmers, cattlemen,

Industry/Entity Type

farming, agriculture, cattle

Coding

Coded - Design and coding required

Requirements
Must have
• about page, contact page, sires page, dams page, SALE page.
Nice to have
• country/farm vibe, barbed wire, wood,

```html
<!DOCTYPE html>
<html lang="en">
<head>
<meta charset="utf-8">
<title>Birchwell Hollow Cattle Company</title>
<link rel="stylesheet" href="https://fonts.googleapis.com/css2?family=Oswald:wght@500;600&family=Inter:wght@400;500;600;700&display=swap">
<style>
:root{
  --gold:#c4922a;
  --gold-light:#e9d98a;
  --ink:#1b1b1b;
  --text:#3a3a3a;
  --panel:#474747;
  --footer:#1c1c1c;
  --white:#ffffff;
}
*{box-sizing:border-box;margin:0;padding:0}
html,body{width:1200px;height:3841px;overflow:hidden}
body{position:relative;background:var(--white);font-family:"Inter",sans-serif;color:var(--text)}
.abs{position:absolute}
.heading{font-family:"Oswald",sans-serif;font-weight:500;color:var(--ink);text-transform:uppercase;letter-spacing:-.2px}
.rule{width:75px;height:4px;background:var(--gold);border-radius:2px}
.btn{display:flex;align-items:center;justify-content:center;gap:8px;background:var(--gold);color:var(--white);font-weight:700;font-size:14px;border-radius:22px;text-transform:uppercase;letter-spacing:.2px}
.btn svg{width:16px;height:10px}
.body-copy{font-size:13.4px;line-height:22.5px;text-align:justify;color:var(--text)}

/* hero */
.hero{left:0;top:0;width:1200px;height:740px;background:linear-gradient(180deg,#6f8fb0 0%,#a9b9c4 18%,#c7c1a4 27%,#5f7a47 34%,#4a7a2e 55%,#3e6b26 100%)}
.nav-bar{left:149px;top:82px;width:901px;height:60px;background:var(--white);border-radius:30px}
.nav-link{top:103px;font-size:14px;color:var(--ink)}
.nav-link.active{color:var(--gold)}
.nav-logo{left:515px;top:16px;width:170px;height:170px;border-radius:50%;background:var(--white);display:flex;flex-direction:column;align-items:center;justify-content:center;text-align:center}
.nav-logo .name{font-family:"Oswald",sans-serif;font-weight:600;font-size:20px;line-height:22px;color:var(--ink);text-transform:uppercase;margin-top:30px}
.nav-cta{left:920px;top:90px;width:124px;height:44px;font-size:14px}
.hero-title{left:0;top:250px;width:1200px;text-align:center;color:var(--white);font-size:48px;line-height:58px}
.hero-title span{display:inline-block;border-bottom:2px solid var(--white);line-height:54px}
.hero-sub{left:0;top:390px;width:1200px;text-align:center;color:var(--white);font-size:16px;line-height:24px}
.hero-btn{left:487px;top:467px;width:226px;height:42px}

/* about */
.about-photo{left:661px;top:820px;width:408px;height:408px;border-radius:50%;border:3px solid var(--gold-light);background:linear-gradient(160deg,#6b5440 0%,#8b6c50 40%,#5b4a3c 75%,#d8d2c6 100%)}
.about-seal{left:630px;top:1055px;width:180px;height:180px;border-radius:50%;background:#1a1612;border:4px solid var(--gold);display:flex;align-items:center;justify-content:center;text-align:center;padding:20px;font-family:"Oswald",sans-serif;font-size:19px;line-height:23px;color:var(--gold);text-transform:uppercase}

/* sires */
.card{top:1448px;width:282px;height:383px;background:var(--white);border-radius:18px;box-shadow:0 4px 14px rgba(0,0,0,.14);overflow:hidden;text-align:center;border:2px solid transparent}
.card.is-active{border-color:var(--gold)}
.card-photo{height:204px}
.card-icon{position:absolute;left:107px;top:170px;width:66px;height:66px;border-radius:50%;background:var(--white);border:3px solid var(--gold-light);display:flex;align-items:center;justify-content:center}
.card.is-active .card-icon{background:var(--gold)}
.card-title{margin-top:56px;font-family:"Oswald",sans-serif;font-weight:500;font-size:17px;color:var(--ink);text-transform:uppercase}
.card-text{margin:14px 22px 0;font-size:12.4px;line-height:18px;color:#4a4a4a}
.arrow{width:48px;height:48px;border-radius:50%;background:#0d0d0d;display:flex;align-items:center;justify-content:center;top:1634px}

/* sale */
.sale{left:0;top:2046px;width:1200px;height:528px;background:linear-gradient(180deg,#2a2a29 0%,#33312d 50%,#262523 100%)}
.sale-text{left:200px;top:2270px;width:800px;text-align:center;color:var(--white);font-size:13.4px;line-height:26.5px}

/* frozen */
.frozen-photo{left:152px;top:2666px;width:420px;height:420px;border-radius:50%;border:3px solid var(--gold-light);background:radial-gradient(circle at 50% 60%,#e9dccb 0%,#b9b4ac 35%,#4f6f99 75%,#2d4b7c 100%)}

/* newsletter */
.signup{left:149px;top:3206px;width:901px;height:262px;background:var(--panel);border-radius:36px}
.signup-input{left:298px;top:3355px;width:591px;height:52px;border-radius:26px;background:var(--white);border:3px solid #d7d7d7;font-size:13px;color:#333;display:flex;align-items:center;padding-left:18px}
.signup-btn{left:740px;top:3360px;width:143px;height:42px}

/* footer */
.footer{left:0;top:3440px;width:1200px;height:401px}
.footer-logo{left:150px;top:3590px;width:285px;text-align:center;color:var(--white);font-family:"Oswald",sans-serif;font-weight:500;text-transform:uppercase}
.footer-nav{top:3580px;font-size:15px;color:var(--white)}
.contact-dot{width:46px;height:46px;border-radius:50%;background:var(--gold);display:flex;align-items:center;justify-content:center;top:3651px}
.contact-label{font-size:14px;color:var(--white);line-height:22px}
.contact-label b{font-weight:600}
</style>
</head>
<body>

<!-- hero -->
<div class="abs hero" role="img" aria-label="Photo of cattle grazing on a green pasture under a bright sky"></div>
<svg class="abs" style="left:0;top:580px" width="1200" height="162" viewBox="0 0 1200 162">
  <path d="M0 145 C60 110 110 95 160 110 C210 125 240 70 300 40 C330 25 345 20 360 34 C380 55 420 70 470 80 C540 92 590 60 640 40 C680 25 700 60 730 75 C750 40 770 5 790 25 C800 60 820 95 860 70 C900 45 950 70 1000 85 C1060 100 1120 95 1200 80 L1200 162 L0 162 Z" fill="#fff"/>
  <circle cx="150" cy="123" r="12" fill="#fff"/><circle cx="335" cy="112" r="26" fill="#fff"/><circle cx="455" cy="114" r="12" fill="#fff"/>
  <circle cx="935" cy="150" r="22" fill="#fff"/><circle cx="1185" cy="130" r="10" fill="#fff"/>
</svg>
<div class="abs nav-bar"></div>
<div class="abs nav-link active" style="left:187px">Home</div>
<div class="abs nav-link" style="left:258px">About</div>
<div class="abs nav-link" style="left:330px">Sires</div>
<div class="abs nav-link" style="left:396px">Dams</div>
<div class="abs nav-link" style="left:739px">Sale</div>
<div class="abs nav-link" style="left:799px">Frozen Genetics</div>
<div class="abs btn nav-cta">Contact <svg viewBox="0 0 16 10"><path d="M0 5h13M9 1l4 4-4 4" stroke="#fff" stroke-width="2" fill="none"/></svg></div>
<div class="abs nav-logo"><div class="name">Birchwell<br>Hollow</div></div>
<h1 class="abs heading hero-title" style="color:#fff"><span>Raising Quality Angus</span><br><span>With Integrity and Tradition</span></h1>
<p class="abs hero-sub">Birchwell Hollow Cattle Company is dedicated to producing structurally sound,<br>performance-driven Angus genetics built for longevity and productivity.</p>
<div class="abs btn hero-btn">View Sale Cattle <svg viewBox="0 0 16 10"><path d="M0 5h13M9 1l4 4-4 4" stroke="#fff" stroke-width="2" fill="none"/></svg></div>

<!-- about -->
<h2 class="abs heading" style="left:151px;top:860px;font-size:42px">About Us</h2>
<div class="abs rule" style="left:151px;top:923px"></div>
<p class="abs body-copy" style="left:151px;top:951px;width:427px">Sed ut perspiciatis unde omnis iste natus error sit voluptatem accusantium doloremque laudantium, totam rem aperiam, eaque ipsa quae ab illo inventore veritatis et quasi architecto beatae vitae dicta sunt explicabo. Nemo enim ipsam voluptatem quia voluptas sit aspernatur aut odit aut fugit, sed quia consequuntur magni dolores eos qui ratione voluptatem sequi nesciunt. Neque porro quisquam est, qui dolorem ipsum quia dolor sit amet, consectetur, adipisci velit, sed quia non numquam eius modi tempora incidunt ut labore et dolore magnam aliquam quaerat voluptatem.</p>
<div class="abs btn" style="left:151px;top:1176px;width:165px;height:42px">Learn More <svg viewBox="0 0 16 10"><path d="M0 5h13M9 1l4 4-4 4" stroke="#fff" stroke-width="2" fill="none"/></svg></div>
<div class="abs about-photo" role="img" aria-label="Family photo of the ranch owners with their children and dog in front of a wooden barn"></div>
<div class="abs about-seal">Birchwell Hollow</div>

<!-- sires -->
<h2 class="abs heading" style="left:0;top:1345px;width:1200px;text-align:center;font-size:42px">Featured Sires</h2>
<div class="abs rule" style="left:562px;top:1410px"></div>
<div class="abs arrow" style="left:76px"><svg width="14" height="22" viewBox="0 0 14 22"><path d="M11 2 3 11l8 9" stroke="#fff" stroke-width="2" fill="none"/></svg></div>
<div class="abs arrow" style="left:1068px"><svg width="14" height="22" viewBox="0 0 14 22"><path d="M3 2l8 9-8 9" stroke="#fff" stroke-width="2" fill="none"/></svg></div>

<div class="abs card" style="left:150px">
  <div class="card-photo" role="img" aria-label="Cattle eating from a single round bale feeder" style="background:linear-gradient(180deg,#5b6b4a,#7a5a3c 60%,#8d7650)"></div>
  <div class="card-icon"><svg width="36" height="30" viewBox="0 0 36 30" fill="none" stroke="#333" stroke-width="1.6"><ellipse cx="18" cy="15" rx="14" ry="11"/><ellipse cx="18" cy="15" rx="8" ry="6"/><circle cx="18" cy="15" r="2"/></svg></div>
  <div class="card-title">Single Bale Feeder</div>
  <p class="card-text">Lorem Ipsum Dolor Sit Amet, Consectetur Adipiscing Elit, Sed Do Eiusmod Tempor Incididunt Ut Labore Et Dolore Magna Aliqua.</p>
</div>
<div class="abs card is-active" style="left:458px">
  <div class="card-photo" role="img" aria-label="Hereford cow beside a double bale feeder" style="background:linear-gradient(180deg,#6a5a48,#5a3a28 55%,#3a2c22)"></div>
  <div class="card-icon"><svg width="34" height="30" viewBox="0 0 34 30" fill="none" stroke="#fff" stroke-width="1.6"><rect x="4" y="4" width="12" height="22" rx="3"/><rect x="18" y="4" width="12" height="22" rx="3"/></svg></div>
  <div class="card-title">Double Bale Feeder</div>
  <p class="card-text">Lorem Ipsum Dolor Sit Amet, Consectetur Adipiscing Elit, Sed Do Eiusmod Tempor Incididunt Ut Labore Et Dolore Magna Aliqua.</p>
</div>
<div class="abs card" style="left:766px">
  <div class="card-photo" role="img" aria-label="Young cattle feeding at a triple bale feeder" style="background:linear-gradient(180deg,#5d6a72,#6b4a34 55%,#7b6a50)"></div>
  <div class="card-icon"><svg width="36" height="30" viewBox="0 0 36 30" fill="none" stroke="#333" stroke-width="1.6"><circle cx="9" cy="20" r="6"/><circle cx="27" cy="20" r="6"/><circle cx="18" cy="9" r="6"/></svg></div>
  <div class="card-title">Triple Bale Feeder</div>
  <p class="card-text">Lorem Ipsum Dolor Sit Amet, Consectetur Adipiscing Elit, Sed Do Eiusmod Tempor Incididunt Ut Labore Et Dolore Magna Aliqua.</p>
</div>
<div class="abs btn" style="left:504px;top:1883px;width:203px;height:42px">View All Sires <svg viewBox="0 0 16 10"><path d="M0 5h13M9 1l4 4-4 4" stroke="#fff" stroke-width="2" fill="none"/></svg></div>

<!-- sale -->
<div class="abs sale" role="img" aria-label="Dimmed photo of cattle standing in a snowy field"></div>
<h2 class="abs heading" style="left:0;top:2160px;width:1200px;text-align:center;font-size:42px;color:#fff">Current Sale Cattle</h2>
<div class="abs rule" style="left:562px;top:2226px"></div>
<p class="abs sale-text">Sed ut perspiciatis unde omnis iste natus error sit voluptatem accusantium doloremque laudantium, totam rem aperiam, eaque ipsa quae ab illo inventore veritatis et quasi architecto beatae vitae dicta sunt explicabo. Nemo enim ipsam voluptatem quia voluptas sit aspernatur aut odit aut fugit, sed quia consequuntur magni dolores eos qui ratione voluptatem sequi nesciunt. Neque porro quisquam est, qui dolorem ipsum quia dolor sit amet, consectetur,</p>
<div class="abs btn" style="left:504px;top:2427px;width:203px;height:42px">View Sale <svg viewBox="0 0 16 10"><path d="M0 5h13M9 1l4 4-4 4" stroke="#fff" stroke-width="2" fill="none"/></svg></div>

<!-- frozen genetics -->
<div class="abs frozen-photo" role="img" aria-label="Photo of glass sample jars on a lab rack for frozen genetics"></div>
<h2 class="abs heading" style="left:620px;top:2690px;font-size:42px">Frozen Genetics</h2>
<div class="abs rule" style="left:620px;top:2754px"></div>
<p class="abs body-copy" style="left:620px;top:2783px;width:425px">Sed ut perspiciatis unde omnis iste natus error sit voluptatem accusantium doloremque laudantium, totam rem aperiam, eaque ipsa quae ab illo inventore veritatis et quasi architecto beatae vitae dicta sunt explicabo. Nemo enim ipsam voluptatem quia voluptas sit aspernatur aut odit aut fugit, sed quia consequuntur magni dolores eos qui ratione voluptatem sequi nesciunt. Neque porro quisquam est, qui dolorem ipsum quia dolor sit amet, consectetur, adipisci velit, sed quia non numquam eius modi tempora incidunt ut labore et dolore magnam aliquam quaerat voluptatem.</p>
<div class="abs btn" style="left:620px;top:3008px;width:163px;height:42px">Learn More <svg viewBox="0 0 16 10"><path d="M0 5h13M9 1l4 4-4 4" stroke="#fff" stroke-width="2" fill="none"/></svg></div>

<!-- footer -->
<svg class="abs footer" viewBox="0 0 1200 401">
  <path d="M0 52 C40 40 70 25 110 40 C150 55 180 60 230 50 C300 35 360 60 430 55 C520 48 600 58 700 52 C800 46 880 60 950 50 C1020 40 1090 25 1130 40 C1160 50 1180 38 1200 30 L1200 401 L0 401 Z" fill="var(--footer)"/>
  <circle cx="118" cy="44" r="9" fill="#fff"/><circle cx="290" cy="46" r="7" fill="#fff"/><circle cx="940" cy="82" r="18" fill="#fff"/><circle cx="1188" cy="40" r="6" fill="#fff"/><circle cx="455" cy="82" r="4" fill="#fff"/><circle cx="120" cy="90" r="4" fill="#fff"/>
</svg>
<div class="abs signup"></div>
<h2 class="abs heading" style="left:149px;top:3250px;width:901px;text-align:center;font-size:42px;color:#fff">Stay Connected With Birchwell Hollow</h2>
<div class="abs rule" style="left:562px;top:3316px"></div>
<div class="abs signup-input">Full Name</div>
<div class="abs btn signup-btn">Submit <svg viewBox="0 0 16 10"><path d="M0 5h13M9 1l4 4-4 4" stroke="#fff" stroke-width="2" fill="none"/></svg></div>

<div class="abs footer-logo"><div style="font-size:38px;line-height:44px">Birchwell Hollow</div><div style="font-size:20px;letter-spacing:5px;margin-top:6px">Cattle Company</div></div>
<div class="abs footer-nav" style="left:551px">Home</div>
<div class="abs footer-nav" style="left:626px">About</div>
<div class="abs footer-nav" style="left:702px">Sires</div>
<div class="abs footer-nav" style="left:771px">Dams</div>
<div class="abs footer-nav" style="left:849px">Sale</div>
<div class="abs footer-nav" style="left:914px">Frozen Genetics</div>
<div class="abs contact-dot" style="left:547px"><svg width="18" height="18" viewBox="0 0 24 24"><path d="M6.6 10.8a15 15 0 0 0 6.6 6.6l2.2-2.2c.3-.3.7-.4 1-.2 1.1.4 2.3.6 3.6.6.6 0 1 .4 1 1V20c0 .6-.4 1-1 1A17 17 0 0 1 3 4c0-.6.4-1 1-1h3.5c.6 0 1 .4 1 1 0 1.3.2 2.5.6 3.6.1.3 0 .7-.2 1z" fill="#fff"/></svg></div>
<div class="abs contact-label" style="left:610px;top:3650px"><b>Call Us:</b><br>+1 250-555-0148</div>
<div class="abs contact-dot" style="left:754px"><svg width="18" height="14" viewBox="0 0 20 14" fill="none" stroke="#fff" stroke-width="1.6"><rect x="1" y="1" width="18" height="12" rx="1.5"/><path d="M1 2l9 6 9-6"/></svg></div>
<div class="abs contact-label" style="left:818px;top:3650px"><b>Email Us:</b><br>hello@birchwellhollow.ca</div>
<div class="abs" style="left:455px;top:3722px;width:595px;height:1px;background:#4a4a4a"></div>
<div class="abs" style="left:700px;top:3752px;width:345px;text-align:right;font-size:12px;color:#fff">© 2026 All Rights Reserved | Company Name</div>

</body>
</html>
```